Los Brava Dip – CPG Website with WordPress - Store Locator: WP Maps plugin

Larkfield Food Company is a startup consumer packaged goods (CPG) brand launching its flagship product line — Los Brava Dip. We’re seeking a talented web designer to create a bold, professional, mobile-optimized website using WordPress with a WP Maps store locator to help customers find local retailers.

Our goal is to build a strong online presence that supports both retail growth and direct-to-consumer sales.

See Los Brava _Website_Design_Brief word document.

The website URL is https://losbravadip.example/

Target Market(s)

Consumers of gourmet salsa

Industry/Entity Type

Consumer Packaged Goods - Salsa manufacturer.

Coding

Coded - Design and coding required

Number of Pages Required

5+ page

Requirements
Must have
• The design of the Los Brava Dip website shall emulate the clean, polished aesthetic of Fennigo.example.

```html
<!DOCTYPE html>
<html lang="en">
<head>
<meta charset="utf-8">
<title>Los Brava Dip – Turn Up The Flavor</title>
<link rel="stylesheet" href="https://fonts.googleapis.com/css2?family=Playfair+Display:wght@500;600;700;800&family=Poppins:wght@400;500;600&display=swap">
<style>
:root{
  --teal-deep:#132a2c;
  --teal:#17424a;
  --teal-btn:#15434a;
  --red:#c94324;
  --red-logo:#c8292a;
  --yellow:#f1b43a;
  --green:#3f6b1f;
  --mint-a:#eef8e2;
  --mint-b:#dff8b6;
  --text:#1f3b3e;
  --white:#ffffff;
}
*{box-sizing:border-box;margin:0;padding:0}
html,body{width:1200px;height:3575px;overflow:hidden}
body{position:relative;font-family:"Poppins",sans-serif;color:var(--text);background:var(--white)}
.abs{position:absolute}
.serif{font-family:"Playfair Display",serif}
.btn{position:absolute;display:flex;align-items:center;justify-content:center;gap:14px;border-radius:24px;color:var(--white);font-weight:600;font-size:16px;box-shadow:0 5px 10px rgba(0,0,0,.22)}
.btn svg{width:20px;height:20px;fill:none;stroke:currentColor;stroke-width:2}
.btn--red{background:var(--red)}
.btn--teal{background:var(--teal-btn)}
.btn--yellow{background:var(--yellow)}
.btn--green{background:var(--green)}

/* hero */
.hero{left:0;top:0;width:1200px;height:688px;background:radial-gradient(ellipse at 80% 45%,#1f5a5e 0%,#173c40 40%,#141d1f 85%)}
.logo{font-family:"Playfair Display",serif;font-weight:700;color:var(--red-logo)}
.hero .logo{left:111px;top:44px;font-size:38px}
.nav{left:293px;top:60px;display:flex;gap:21px;font-size:16px;color:var(--white)}
.nav a{color:inherit;text-decoration:none;position:relative}
.nav a.active::after{content:"";position:absolute;left:18px;top:26px;width:14px;height:3px;border-radius:2px;background:var(--red)}
.nav-icons{left:994px;top:60px;display:flex;gap:18px}
.nav-icons svg{width:22px;height:22px;fill:none;stroke:var(--white);stroke-width:1.8}
.hero-title{left:111px;top:218px;font-family:"Playfair Display",serif;font-weight:800;font-size:82px;line-height:1.12}
.hero-title .l1{color:var(--red);display:block}
.hero-title .l2{color:var(--yellow);display:block;padding-left:32px}
.hero-copy{left:113px;top:420px;width:500px;font-size:16.5px;line-height:29px;color:var(--white)}
.food-ring{left:444px;top:194px;width:334px;height:125px;border-radius:63px;border:2px solid #8a8a3a;background:#1c2b2b}
.food{position:absolute;top:12px;width:100px;height:100px;border-radius:50%}
.jars{left:673px;top:312px;width:485px;height:291px}
.jar{position:absolute;border-radius:26px 26px 34px 34px}

/* featured */
.feat-band{left:42px;top:688px;width:1116px;height:484px}
.pill{position:absolute;display:flex;align-items:center;justify-content:center;gap:28px;border-radius:32px;font-family:"Playfair Display",serif;font-weight:600}
.pill::before,.pill::after{content:"";width:9px;height:9px;border-radius:50%;background:currentColor}
.feat-pill{left:345px;top:770px;width:509px;height:62px;border:1.5px solid #b8c84a;color:#d7e66a;font-size:38px}
.card{position:absolute;top:936px;width:294px;height:441px;background:var(--white);border-radius:30px;box-shadow:0 6px 20px rgba(0,0,0,.12)}
.card-inner{position:absolute;left:15px;top:15px;right:15px;bottom:18px;border-radius:30px;border:1.5px solid}
.card-jar{position:absolute;left:91px;top:50px;width:112px;height:190px;border-radius:18px 18px 26px 26px}
.card-name{position:absolute;left:0;right:0;top:275px;text-align:center;font-family:"Playfair Display",serif;font-weight:500;font-size:28px;color:var(--text)}
.card .btn{left:62px;top:342px;width:170px;height:46px}

/* reviews */
.reviews{left:0;top:1560px;width:1200px;height:891px;background:linear-gradient(100deg,var(--mint-a) 0%,#f1fae4 40%,var(--mint-b) 100%)}
.rev-pill{left:393px;top:1630px;width:416px;height:62px;border:1.5px solid var(--text);color:var(--text);font-size:38px}
.rev-photo{left:111px;top:1755px;width:408px;height:316px;border-radius:30px;background:linear-gradient(120deg,#b5654a 0%,#cf8e63 45%,#7f9a55 100%)}
.rev-head{left:580px;top:1778px;font-size:31px;font-weight:500;color:var(--red)}
.rev-text{left:581px;top:1840px;width:500px;font-size:21px;line-height:38px;color:var(--text)}
.results-head{left:0;width:1200px;top:2116px;text-align:center;font-size:31px;font-weight:500;color:var(--yellow)}
.results-text{left:0;width:1200px;top:2184px;text-align:center;font-size:20.5px;line-height:38px;color:var(--text)}

/* recipes */
.recipes{left:0;top:2451px;width:1200px;height:778px;background:#fffaf8}
.rec-pill{left:422px;top:2529px;width:356px;height:62px;border:1.5px solid var(--text);color:var(--text);font-size:38px}
.rec-img{position:absolute;top:2659px;width:227px;height:330px}
.rec-name{position:absolute;top:3018px;width:227px;text-align:center;font-size:21px;font-weight:500;color:var(--text)}
.rec-btn{top:3082px;width:199px;height:46px}
.arrow{position:absolute;top:2800px;width:28px;height:28px}
.arrow svg{width:28px;height:28px;fill:none;stroke:var(--text);stroke-width:1.8}

/* footer */
.footer{left:0;top:3229px;width:1200px;height:346px;background:var(--teal)}
.footer .logo{left:111px;top:3320px;font-size:70px}
.foot-small{font-size:15px;color:var(--white)}
.foot-title{font-family:"Playfair Display",serif;font-weight:500;font-size:27px;color:var(--white)}
.links{left:444px;top:3348px;display:flex;flex-direction:column;gap:8px;font-size:16px;color:var(--white)}
.field{position:absolute;height:35px;border:1px solid #d9e2e2;border-radius:8px;padding-left:16px;display:flex;align-items:center;font-size:14px;color:#d9e2e2}
.contact-btn{position:absolute;left:889px;top:3395px;width:198px;height:35px;border-radius:8px;background:var(--red);color:var(--white);font-size:15px;font-weight:600;display:flex;align-items:center;justify-content:space-between;padding:0 18px}
</style>
</head>
<body>

<!-- HERO -->
<section class="hero abs">
  <div class="logo abs">Los Brava</div>
  <nav class="nav abs">
    <a class="active">Home</a><a>About</a><a>Featured products</a><a>Where to buy</a><a>Reviews</a><a>Recipes</a><a>Contact</a>
  </nav>
  <div class="nav-icons abs">
    <svg viewBox="0 0 24 24"><circle cx="12" cy="12" r="8"/></svg>
    <svg viewBox="0 0 24 24"><circle cx="12" cy="12" r="9"/><circle cx="12" cy="10" r="3"/><path d="M6.5 18c1.5-2.5 3.5-3.5 5.5-3.5s4 1 5.5 3.5"/></svg>
    <svg viewBox="0 0 24 24"><path d="M3 4h3l2.5 11h10l2-8H7"/><circle cx="10" cy="19" r="1.4"/><circle cx="17" cy="19" r="1.4"/></svg>
  </div>
  <svg class="abs" style="left:750px;top:98px" width="90" height="120" viewBox="0 0 90 120" fill="none" stroke="#cfd8d8" stroke-width="1.3"><path d="M2 118 C40 90 70 60 76 6"/><path d="M70 14 L76 4 L82 14"/></svg>
  <h1 class="hero-title abs"><span class="l1">Turn Up</span><span class="l2">The Flavor</span></h1>
  <p class="hero-copy abs">Crafted with bold spices and real ingredients, Los Brava Dip brings the heat to every table.</p>
  <div class="btn btn--red" style="left:111px;top:513px;width:249px;height:44px">Find a Nearest Store<svg viewBox="0 0 24 24"><circle cx="10" cy="10" r="6"/><path d="M15 15l5 5"/></svg></div>
  <div class="btn btn--teal" style="left:375px;top:513px;width:207px;height:44px;background:#183c40">Shop Products<svg viewBox="0 0 24 24"><path d="M3 4h3l2.5 11h10l2-8H7"/><circle cx="10" cy="19" r="1.4"/><circle cx="17" cy="19" r="1.4"/></svg></div>
  <div class="food-ring abs">
    <div class="food" role="img" aria-label="Plated dish topped with salsa" style="left:12px;background:radial-gradient(#e9d8b8,#b57b44)"></div>
    <div class="food" role="img" aria-label="Stacked tacos with salsa" style="left:86px;background:radial-gradient(#e89a4c,#9a4a1f)"></div>
    <div class="food" role="img" aria-label="Loaded tortilla dish" style="left:160px;background:radial-gradient(#d87a3a,#7a3a1a)"></div>
    <div class="food" role="img" aria-label="Bowl of beans with salsa" style="left:222px;background:radial-gradient(#7a3a2a,#2a2020)"></div>
  </div>
  <div class="jars abs" role="img" aria-label="Three jars of habanero, verde and all natural salsa">
    <div class="jar" style="left:0;top:40px;width:170px;height:245px;background:linear-gradient(#b8952e 0 12%,#d9452a 12%,#c93a1f)"></div>
    <div class="jar" style="left:325px;top:40px;width:165px;height:245px;background:linear-gradient(#b8952e 0 12%,#e36a2a 12%,#c9401f)"></div>
    <div class="jar" style="left:145px;top:5px;width:200px;height:285px;background:linear-gradient(#c9a532 0 12%,#a8b83a 12%,#7c9a2a)"></div>
  </div>
</section>

<!-- FEATURED PRODUCTS -->
<svg class="abs" style="left:0;top:688px" width="1200" height="800" viewBox="0 0 1200 800" fill="none">
  <path d="M24 460 C24 370 60 360 110 360 M1090 360 C1140 360 1176 370 1176 460 C1176 560 1100 610 1090 620 M110 620 C95 600 24 560 24 460" stroke="#4d6e6c" stroke-width="1.3"/>
  <path d="M220 688 C330 735 420 745 470 752 M735 752 C790 745 880 730 980 688" stroke="#4d6e6c" stroke-width="1.3"/>
</svg>
<svg class="feat-band abs" viewBox="0 0 1116 484" role="img" aria-label="Overhead photo of fresh salsa ingredients in a stone bowl">
  <defs><radialGradient id="bandFill" cx="50%" cy="30%" r="70%"><stop offset="0" stop-color="#3f5a45"/><stop offset=".6" stop-color="#2b3f36"/><stop offset="1" stop-color="#1d2c2a"/></radialGradient></defs>
  <path d="M0 0 H1116 V404 Q558 560 0 404 Z" fill="url(#bandFill)"/>
</svg>
<h2 class="pill feat-pill">Our Featured Products</h2>

<div class="card" style="left:111px">
  <div class="card-inner" style="border-color:#f0c96a"></div>
  <div class="card-jar" role="img" aria-label="All natural salsa jar" style="background:linear-gradient(#c9a532 0 14%,#e0642a 14%,#c8401f)"></div>
  <div class="card-name">All Natural Salsa</div>
  <div class="btn btn--yellow">Shop Now<svg viewBox="0 0 24 24"><path d="M3 4h3l2.5 11h10l2-8H7"/><circle cx="10" cy="19" r="1.4"/><circle cx="17" cy="19" r="1.4"/></svg></div>
</div>
<div class="card" style="left:454px">
  <div class="card-inner" style="border-color:#4f7a34"></div>
  <div class="card-jar" role="img" aria-label="Verde salsa jar" style="background:linear-gradient(#c9a532 0 14%,#a9bd48 14%,#6f9a2e)"></div>
  <div class="card-name">Verde Salsa</div>
  <div class="btn btn--green">Shop Now<svg viewBox="0 0 24 24"><path d="M3 4h3l2.5 11h10l2-8H7"/><circle cx="10" cy="19" r="1.4"/><circle cx="17" cy="19" r="1.4"/></svg></div>
</div>
<div class="card" style="left:795px">
  <div class="card-inner" style="border-color:#d5523a"></div>
  <div class="card-jar" role="img" aria-label="Habanero salsa jar" style="background:linear-gradient(#c9a532 0 14%,#de4a2a 14%,#b8321c)"></div>
  <div class="card-name">Habanero Salsa</div>
  <div class="btn btn--red">Shop Now<svg viewBox="0 0 24 24"><path d="M3 4h3l2.5 11h10l2-8H7"/><circle cx="10" cy="19" r="1.4"/><circle cx="17" cy="19" r="1.4"/></svg></div>
</div>
<div class="btn btn--teal" style="left:465px;top:1422px;width:270px;height:44px">Find the Nearest Store<svg viewBox="0 0 24 24"><circle cx="10" cy="10" r="6"/><path d="M15 15l5 5"/></svg></div>

<!-- REVIEWS -->
<section class="reviews abs"></section>
<h2 class="pill rev-pill">Product Reviews</h2>
<div class="rev-photo abs" role="img" aria-label="Blindfolded taster being fed salsa at a picnic table"></div>
<h3 class="rev-head abs">Blind Taste Test – June 2025</h3>
<p class="rev-text abs">In June 2025, Los Brava Dip was put to the test in a blind taste challenge conducted by a third party with 38 participants. Without knowing the brand, tasters judged flavor, heat level balance, aroma, appearance, and overall satisfaction.</p>
<h3 class="results-head abs">And The Results ?</h3>
<p class="results-text abs">An impressive 4.67 out of 5 stars, with 89% of participants rating it 5 stars.<br>Our reviews reflect the authentic flavor and bold character that make<br>Los Brava stand out in a crowded salsa market. Taste-tested, crowd-approved.</p>
<div class="btn btn--teal" style="left:458px;top:2336px;width:284px;height:44px">Read Reviews and Stats<svg viewBox="0 0 24 24"><path d="M4 20h16M7 17v-5M11 17V8M15 17v-7M19 17V6"/></svg></div>

<!-- RECIPES -->
<section class="recipes abs"></section>
<h2 class="pill rec-pill">Best Recipes</h2>
<div class="arrow" style="left:40px"><svg viewBox="0 0 28 28"><circle cx="14" cy="14" r="12"/><path d="M20 14H8M12 10l-4 4 4 4"/></svg></div>
<div class="arrow" style="left:1132px"><svg viewBox="0 0 28 28"><circle cx="14" cy="14" r="12"/><path d="M8 14h12M16 10l4 4-4 4"/></svg></div>

<div class="rec-img" role="img" aria-label="Mexican beef rice with melted cheese" style="left:111px;background:linear-gradient(160deg,#e6d7c8,#c9692a 55%,#8a3a18)"></div>
<div class="rec-img" role="img" aria-label="Baked chicken salsa on a blue plate" style="left:361px;background:linear-gradient(160deg,#2f5a3a,#c9a56a 50%,#1f3a7a)"></div>
<div class="rec-img" role="img" aria-label="Slow cooked beef salsa bowl with avocado" style="left:611px;background:linear-gradient(160deg,#d9d9d9,#6f8a3a 45%,#2a2a2a)"></div>
<div class="rec-img" role="img" aria-label="Saucy chicken taco" style="left:862px;background:linear-gradient(160deg,#e8a85a,#c9601f 55%,#8a3a1a)"></div>

<div class="rec-name" style="left:111px">Mexican beef rice</div>
<div class="rec-name" style="left:361px">Baked chicken salsa</div>
<div class="rec-name" style="left:611px">Slowcook beef salsa</div>
<div class="rec-name" style="left:862px">Saucy chicken taco</div>

<div class="btn btn--red rec-btn" style="left:125px">Learn Recipe<svg viewBox="0 0 24 24"><path d="M6 13c-2-1-2-5 1-5 0-3 4-4 5-2 1-2 5-1 5 2 3 0 3 4 1 5v5H6z"/></svg></div>
<div class="btn btn--red rec-btn" style="left:375px">Learn Recipe<svg viewBox="0 0 24 24"><path d="M6 13c-2-1-2-5 1-5 0-3 4-4 5-2 1-2 5-1 5 2 3 0 3 4 1 5v5H6z"/></svg></div>
<div class="btn btn--red rec-btn" style="left:625px">Learn Recipe<svg viewBox="0 0 24 24"><path d="M6 13c-2-1-2-5 1-5 0-3 4-4 5-2 1-2 5-1 5 2 3 0 3 4 1 5v5H6z"/></svg></div>
<div class="btn btn--red rec-btn" style="left:876px">Learn Recipe<svg viewBox="0 0 24 24"><path d="M6 13c-2-1-2-5 1-5 0-3 4-4 5-2 1-2 5-1 5 2 3 0 3 4 1 5v5H6z"/></svg></div>

<!-- FOOTER -->
<footer class="footer abs"></footer>
<div class="logo abs" style="left:111px;top:3320px;font-size:64px">Los Brava</div>
<div class="foot-small abs" style="left:112px;top:3459px;display:flex;align-items:center;gap:12px">Follow us on Picturely<svg width="18" height="18" viewBox="0 0 18 18" fill="none" stroke="#fff" stroke-width="1.6"><circle cx="9" cy="9" r="7"/></svg></div>
<div class="foot-small abs" style="left:111px;top:3499px">Copyright © 2025 Los Brava</div>

<h4 class="foot-title abs" style="left:444px;top:3297px">Quick Links</h4>
<div class="links abs"><span>Home</span><span>About</span><span>Featured products</span><span>Where to buy</span><span>Reviews</span><span>Recipes</span></div>

<h4 class="foot-title abs" style="left:682px;top:3297px">Contact Us</h4>
<div class="field" style="left:684px;top:3352px;width:198px">Your name</div>
<div class="field" style="left:889px;top:3352px;width:198px">Your email address</div>
<div class="field" style="left:684px;top:3395px;width:198px">Your phone number</div>
<div class="contact-btn">Contact Now<svg width="28" height="14" viewBox="0 0 28 14" fill="none" stroke="#fff" stroke-width="1.6"><path d="M0 7h26M20 1l6 6-6 6"/></svg></div>
<div class="foot-small abs" style="left:684px;top:3458px;display:flex;align-items:center;gap:14px"><svg width="18" height="14" viewBox="0 0 18 14" fill="none" stroke="#fff" stroke-width="1.5"><rect x="1" y="1" width="16" height="12" rx="1"/><path d="M1 2l8 6 8-6"/></svg>support@losbravadip.example</div>
<div class="foot-small abs" style="left:684px;top:3494px;font-size:14.5px">Privacy policy &nbsp;|&nbsp; Cookies policy &nbsp;|&nbsp; Cookies Settings</div>

</body>
</html>
```